Business Card Design Project

I require a business card with the following information on them for various different people;
name
m:
f:
e:
I have a logo already and will attached that. We are in the construction industry. I require something clean and simple but eye catching at the same time. You can use another colour with our logo if you like and you can style the logo as well if you wish. I am open.
Also it needs to be front and back design.
Industry/Entity Type
Construction
Requirements
Must have
- Logo, name, mobile, fax and email address.
Front and back design

```html
<!DOCTYPE html>
<html lang="en">
<head>
<meta charset="utf-8">
<title>Stonebridge Builders – Business Cards</title>
<link rel="stylesheet" href="https://fonts.googleapis.com/css2?family=Open+Sans:wght@400;600&display=swap">
<style>
  :root {
    --green: #4fae3e;
    --green-light: #a9d45a;
    --ink: #3d3d3d;
    --card: #ffffff;
    --edge: #4a4a4a;
    --backdrop: #ecebe8;
    --silver-1: #fafafa;
    --silver-2: #c9cbce;
  }
  * { margin: 0; padding: 0; box-sizing: border-box; }
  html, body { width: 1200px; height: 757px; overflow: hidden; }
  body {
    background: var(--backdrop);
    font-family: "Open Sans", Arial, sans-serif;
    position: relative;
  }
  .card {
    position: absolute;
    width: 513px;
    height: 292px;
    background: var(--card);
    border: 1px solid var(--edge);
    overflow: hidden;
  }
  .card--front { left: 63px; top: 61px; }
  .card--back { left: 623px; top: 61px; }
  .card--feature {
    left: 342px; top: 402px;
    background: linear-gradient(135deg, var(--silver-1) 0%, #e6e7e8 45%, var(--silver-2) 100%);
  }

  .wordmark {
    position: absolute;
    display: flex;
    align-items: center;
    gap: 12px;
    color: var(--green);
    font-weight: 400;
    white-space: nowrap;
  }
  .wordmark__square {
    width: 30px; height: 30px;
    background: var(--green);
    border-radius: 3px;
  }
  .card--front .wordmark { left: 50%; top: 62px; transform: translateX(-50%); font-size: 34px; }
  .card--back .wordmark { left: 50%; top: 130px; transform: translateX(-50%); font-size: 34px; }
  .card--feature .wordmark { right: 28px; top: 196px; font-size: 30px; }
  .card--feature .wordmark__square { width: 26px; height: 26px; }

  .tab {
    position: absolute;
    width: 11px;
    background: linear-gradient(180deg, var(--green-light), var(--green));
  }
  .tab--left { left: 0; top: 163px; height: 104px; border-radius: 0 8px 8px 0; }
  .tab--right { right: 0; top: 175px; height: 57px; border-radius: 8px 0 0 8px; }

  .contact {
    position: absolute;
    left: 25px; top: 188px;
    list-style: none;
    font-size: 12.5px;
    color: var(--ink);
    line-height: 21px;
  }
  .contact li { display: flex; align-items: center; gap: 6px; }
  .contact svg { width: 9px; height: 9px; fill: var(--ink); }

  .person {
    position: absolute;
    right: 20px; top: 193px;
    font-size: 15px;
    color: var(--green);
  }
  .person__name { font-weight: 600; }
  .person__title { font-weight: 400; font-size: 14px; }
</style>
</head>
<body>

<section class="card card--front">
  <div class="wordmark"><span class="wordmark__square"></span>Stonebridge Builders</div>
  <span class="tab tab--left"></span>
  <span class="tab tab--right"></span>
  <ul class="contact">
    <li><svg viewBox="0 0 10 10" aria-label="mobile"><rect x="2" y="0" width="6" height="10" rx="1"/></svg>+91 98450 21736</li>
    <li><svg viewBox="0 0 10 10" aria-label="fax"><rect x="0" y="4" width="10" height="6" rx="1"/><rect x="2" y="0" width="6" height="4"/></svg>+91 98450 21736</li>
    <li><svg viewBox="0 0 10 10" aria-label="email"><rect x="0" y="2" width="10" height="6"/></svg>office@stonebridgemail.com</li>
  </ul>
  <p class="person"><span class="person__name">Your Name ,</span> <span class="person__title">Title</span></p>
</section>

<section class="card card--back">
  <div class="wordmark"><span class="wordmark__square"></span>Stonebridge Builders</div>
</section>

<section class="card card--feature">
  <div class="wordmark"><span class="wordmark__square"></span>Stonebridge Builders</div>
</section>

</body>
</html>
```